Help design website for "Brightwater Civic Advisors" to advance the common good

Here is the Google doc link that lays out the design:

https://files.plumrivet.example/sheet/d/7QmTzR2wLx9KpVbN4hJcY8sEaUoFdG3iXkMnPq5rWt6/edit?usp=sharing

Here is the Google drive folder with the logos and photos: https://vault.plumrivet.example/open?id=4HkWp9LzQe2TxRvN8mBaYc3DsUoJfG6

The testimonials are being gathered and will be shared by Friday, 1/4.

The winner will also have to migrate the coding files to my hosting site.

Thank you for your help! Looking forward to seeing your designs.

Target Market(s)

Prospective clients

Industry/Entity Type

Non Profit

Coding

Coded - Design and coding required

Number of Pages Required

5+ page

Requirements
Must have
• Noted in the Google doc regarding layout.
Nice to have

```html
<!DOCTYPE html>
<html lang="en">
<head>
<meta charset="utf-8">
<title>Brightwater Civic Advisors – Media &amp; Impact</title>
<link rel="stylesheet" href="https://fonts.googleapis.com/css2?family=Poppins:wght@500;600;700&family=Open+Sans:wght@400&display=swap">
<style>
  :root {
    --brand-blue: #3a87cc;
    --ink: #111317;
    --body-text: #2c2d31;
    --footer-dark: #25262e;
    --band-grey: #eef0f3;
    --white: #ffffff;
    --card-shadow: 0 2px 8px rgba(0,0,0,0.12);
  }
  * { margin: 0; padding: 0; box-sizing: border-box; }
  html, body { width: 690px; height: 1200px; overflow: hidden; background: var(--white); }
  .page { position: relative; width: 690px; height: 1200px; overflow: hidden; font-family: "Open Sans", Arial, sans-serif; color: var(--body-text); }

  /* Header */
  .site-header { position: absolute; left: 0; top: 0; width: 690px; height: 72px; background: var(--brand-blue); z-index: 3; }
  .brand { position: absolute; display: flex; align-items: center; gap: 10px; font-family: "Poppins", Arial, sans-serif; font-weight: 500; color: var(--white); letter-spacing: 3.2px; text-transform: uppercase; }
  .brand-square { width: 34px; height: 34px; border: 3px solid var(--white); }
  .brand-name { display: flex; flex-direction: column; border-left: 1.5px solid var(--white); padding-left: 8px; }
  .site-header .brand { left: 83px; top: 10px; font-size: 12px; line-height: 15px; }
  .cta-consult { position: absolute; left: 423px; top: 12px; width: 184px; height: 24px; border: 1.6px solid var(--white); color: var(--white); font: 600 8px/21px "Poppins", Arial, sans-serif; text-align: center; text-transform: uppercase; }
  .main-nav a { position: absolute; top: 51px; color: var(--white); font: 600 8px/11px "Poppins", Arial, sans-serif; text-transform: uppercase; text-decoration: none; }
  .main-nav a.is-current { border-bottom: 1px solid var(--white); padding-bottom: 1px; }

  /* Hero */
  .hero { position: absolute; left: 0; top: 72px; width: 690px; height: 330px;
    background: linear-gradient(160deg, #9fa8a3 0%, #6f7472 30%, #3d3b3c 55%, #8a4a45 75%, #7d8683 100%); }
  .hero-edge { position: absolute; left: 0; top: 300px; width: 690px; height: 110px; z-index: 2; }

  /* Articles */
  .section-title { position: absolute; left: 0; top: 366px; width: 690px; text-align: center; font: 700 19px/26px "Poppins", Arial, sans-serif; color: var(--ink); z-index: 3; }
  .title-rule { position: absolute; left: 337px; top: 396px; width: 16px; height: 2px; background: var(--brand-blue); }

  .article-card { position: absolute; top: 436px; width: 252px; height: 493px; background: var(--white); box-shadow: var(--card-shadow); }
  .article-photo { position: relative; width: 252px; height: 205px; }
  .article-photo .shade { position: absolute; left: 0; bottom: 0; width: 100%; height: 70px; background: linear-gradient(to bottom, rgba(0,0,0,0), rgba(0,0,0,0.6)); }
  .photo-caption { position: absolute; left: 17px; bottom: 12px; width: 225px; color: var(--white); font: 700 8.6px/10.6px "Poppins", Arial, sans-serif; text-transform: uppercase; }
  .article-heading { margin: 24px 0 0 17px; width: 232px; font: 700 10.6px/13px "Poppins", Arial, sans-serif; color: var(--ink); }
  .article-body { margin: 11px 0 0 18px; width: 210px; font-size: 7.5px; line-height: 10.2px; }
  .article-body p + p { margin-top: 10px; }
  .btn { display: block; background: var(--brand-blue); color: var(--white); font: 600 8px/22px "Poppins", Arial, sans-serif; text-transform: uppercase; text-align: center; text-decoration: none; }
  .article-card .btn { position: absolute; left: 20px; top: 450px; width: 70px; height: 22px; }

  .view-all { position: absolute; left: 294px; top: 965px; width: 101px; height: 22px; z-index: 2; }

  /* Footer */
  .band { position: absolute; left: 0; top: 984px; width: 690px; height: 110px; background: var(--band-grey); }
  .footer-shape { position: absolute; left: 0; top: 1020px; width: 690px; height: 180px; }
  .site-footer .brand { left: 82px; top: 1102px; font-size: 15px; line-height: 19px; letter-spacing: 4px; }
  .site-footer .brand-square { width: 46px; height: 46px; border-color: var(--brand-blue); }
  .footer-divider { position: absolute; left: 351px; top: 1098px; width: 1px; height: 82px; background: #4a4b54; }
  .footer-menu-title { position: absolute; left: 386px; top: 1107px; color: var(--white); font: 700 7px/10px "Poppins", Arial, sans-serif; }
  .footer-links { position: absolute; left: 386px; top: 1127px; color: var(--white); font-size: 6.6px; line-height: 10px; text-transform: uppercase; }
  .footer-links span.sep { margin: 0 5px; }
  .copyright { position: absolute; left: 386px; top: 1162px; color: var(--white); font-size: 6.2px; line-height: 9px; }
</style>
</head>
<body>
<div class="page">

  <header class="site-header">
    <div class="brand">
      <span class="brand-square"></span>
      <span class="brand-name"><span>Brightwater</span><span>Civic</span><span>Advisors</span></span>
    </div>
    <a class="cta-consult">Book a complimentary consultation</a>
    <nav class="main-nav">
      <a style="left:323px">About</a>
      <a style="left:368px">Services &amp; Testimonials</a>
      <a style="left:484px" class="is-current">Media &amp; Impact</a>
      <a style="left:568px">Contact</a>
    </nav>
  </header>

  <div class="hero" role="img" aria-label="Photo of volunteers and children in red shirts walking across a city street"></div>
  <svg class="hero-edge" viewBox="0 300 690 110" preserveAspectRatio="none" aria-hidden="true">
    <polygon points="0,374 345,324 690,374 690,410 0,410" fill="#3a87cc"/>
    <polygon points="0,388 345,332 690,388 690,410 0,410" fill="#ffffff"/>
  </svg>

  <h1 class="section-title">Articles</h1>
  <div class="title-rule"></div>

  <article class="article-card" style="left:82px">
    <div class="article-photo" role="img" aria-label="Photo of attendees seated at round tables listening to a speaker" style="background:linear-gradient(150deg,#b7b0a6 0%,#8a7f76 45%,#3f3838 100%)">
      <div class="shade"></div>
      <p class="photo-caption">Attendees listening to a speaker at the Bright Path Work Dinner Dialogue event</p>
    </div>
    <h2 class="article-heading">Residents Meet With Employment Nonprofit</h2>
    <div class="article-body">
      <p>Students and East End community members attended a “Dinner Dialogue” recently featuring the nonprofit Bright Path Works. Conversation centered around the work done by Bright Path Works to help East End residents break the cycle of poverty and unemployment.</p>
      <p>The Dinner Dialogue series, created by the University’s Community Service Center in 2017, seeks to promote the discussion of social justice issues. The meals are hosted three times a quarter at different East End partner organizations, and are open to the public.</p>
      <p>Four of the attendees included Elena Marsh, a RUPD officer and graduate student at the Holloway School; Dana Whitfield, a former Bright Path Works volunteer; and two University students, second-year Clara Novak and third-year Ravi Menon.</p>
    </div>
    <a class="btn">Read more</a>
  </article>

  <article class="article-card" style="left:354px">
    <div class="article-photo" role="img" aria-label="Photo of students performing music in a school gymnasium" style="background:linear-gradient(160deg,#c9c4b8 0%,#3f7d62 40%,#4a4442 70%,#2a2626 100%)">
      <div class="shade"></div>
      <p class="photo-caption">Students performing at the third annual Lindell Park Arts Festival</p>
    </div>
    <h2 class="article-heading">Community and Student Arts Shine<br>at Lindell Park</h2>
    <div class="article-body">
      <p>Every year it gets bigger and better,” said Denise Harlow-Grant, Chief Program Officer of Riverton Youth Programs (RYP), about the third annual Lindell Park Arts Festival that took place last Saturday. A collaboration between RYP, Student Government, the University Community Service Center, and several other university and Lindell Park community organizations, the annual festival once again provided local East End entrepreneurs, residents, and Riverton University students with a place to connect and showcase their artistic skills. The festival was held in the building of Riverton Youth Programs, with a central performance space encircled by booths of local retail vendors.</p>
      <p>Throughout the afternoon, vendors such as Maple Crumb Dessert Shop and Lena’s Kitchen provided free food for the event while schoolkids ran around the space, sitting down periodically to watch performances.</p>
    </div>
    <a class="btn">Read more</a>
  </article>

  <div class="band"></div>
  <a class="btn view-all">View all articles</a>

  <footer class="site-footer">
    <svg class="footer-shape" viewBox="0 1020 690 180" preserveAspectRatio="none" aria-hidden="true">
      <polygon points="0,1085 345,1024 690,1085 690,1200 0,1200" fill="#25262e"/>
    </svg>
    <div class="brand">
      <span class="brand-square"></span>
      <span class="brand-name"><span>Brightwater</span><span>Civic</span><span>Advisors</span></span>
    </div>
    <div class="footer-divider"></div>
    <p class="footer-menu-title">MENU</p>
    <p class="footer-links">About<span class="sep">|</span>Services &amp; Testimonials<span class="sep">|</span>Media &amp; Impact<span class="sep">|</span>Contact</p>
    <p class="copyright">Copyrights @ 2019 All Rights Reserved</p>
  </footer>

</div>
</body>
</html>
```